Need a brochure design for my business which sells Australian themed Christmas ornaments.

We need a brochure designed for our company called Wattle Lantern Pty Ltd.
Our company sells Australian themed glass Christmas ornaments which have been internally hand painted with designs depicting Australian flora & fauna as well as Indigenous art designs. Our website, www.wattlelantern.com.au will show you the product we sell. We would like a brochure to display our current designs (19 in total). Six of the designs have a front & back image. Each design image will be accompanied with a short description of what the design represents. The ornaments each present with a padded gift box for storage and a descriptive swing tag.
We would like to use the same colours of our website (blue and yellow) and would like to incorporate the company logo. We would like the brochure to communicate that all designs have been reproduced from commissioned art work by Australian Indigenous and non-Indigenous artists. The descriptive words unique, Australian, quality, keepsake, gift and beautiful should all be used.
Our website and contact details are also to be included. (See attached files for reference).
The brochure will be distributed to both wholesale and retail clients..
Updates

Project Deadline Extended
Reason: Additional detail required. Thank you

Target Market(s)

Wholesale and retail gift shop clients

Industry/Entity Type

Retail

Requirements
Must have
• All 19 designs must be depicted. All design descriptions must be included. An image example of the padded gift box and swing tag must be included.
The company Logo must be used, preferably at the top of the page.
Must state that all designs have been reproduced from commissioned artwork by Australian Indigenous and non-Indigenous artists.
The descriptive words: Australian design, unique, internally hand-painted, gift, keepsake and beautiful must be used.
The blue and yellow colours (as depicted on the website) must be used. Ideally the brochure would be a two page document (front and back) of one sheet but I will leave the size up to you depending on the design.
Website and contact details.

```html
<!DOCTYPE html>
<html lang="en">
<head>
<meta charset="utf-8">
<title>Wattle Lantern – Brochure</title>
<link rel="stylesheet" href="https://fonts.googleapis.com/css2?family=Open+Sans:wght@300;400;600&family=Great+Vibes&display=swap">
<style>
  :root {
    --backdrop: #2b2e30;
    --paper: #ffffff;
    --brand-blue: #23479b;
    --brand-gold: #e0952f;
    --gold-tint: #f6e3c6;
    --photo-warm: #c9a98c;
    --photo-sky: #7fb6d8;
    --ink: #3a3a3a;
    --muted: #a6a6a6;
  }
  * { margin: 0; padding: 0; box-sizing: border-box; }
  html, body { width: 1200px; height: 900px; overflow: hidden; }
  body {
    background: var(--backdrop);
    font-family: "Open Sans", Arial, sans-serif;
    position: relative;
  }
  .page {
    position: absolute;
    width: 467px;
    height: 662px;
    background: var(--paper);
    box-shadow: 0 4px 14px rgba(0,0,0,.45);
    overflow: hidden;
  }
  .page--front { left: 79px; top: 55px; }
  .page--back { left: 610px; top: 190px; }

  .brand {
    position: absolute;
    display: flex;
    align-items: center;
    gap: 6px;
    font-size: 15px;
    font-weight: 600;
    color: var(--brand-blue);
    white-space: nowrap;
  }
  .brand__dot {
    width: 12px; height: 12px; border-radius: 50%;
    background: var(--brand-gold);
  }
  .page--front .brand { left: 50%; top: 42px; transform: translateX(-50%); }
  .page--back .brand { left: 28px; top: 60px; }

  .ornament {
    position: absolute;
    border-radius: 40px;
    background: radial-gradient(ellipse at center, #fff 45%, var(--gold-tint) 100%);
  }
  .frame {
    position: absolute;
    border: 5px solid var(--brand-gold);
    background: #f1efed;
  }
  .photo { position: absolute; }

  .page--front .ornament { left: 42px; top: 115px; width: 376px; height: 356px; }
  .page--front .frame { left: 99px; top: 157px; width: 261px; height: 261px; }
  .page--front .photo {
    left: 13px; top: 12px; width: 225px; height: 227px;
    background: linear-gradient(170deg, var(--photo-warm) 0%, #d9bfa6 55%, #7fae6a 78%, var(--photo-sky) 100%);
  }
  .photo-caption {
    position: absolute; left: 0; right: 0; top: 20px;
    text-align: center; color: #fff; font-weight: 300;
    font-size: 16px; line-height: 23px;
  }

  .intro {
    position: absolute; left: 10px; right: 10px; top: 500px;
    text-align: center; font-size: 9.2px; line-height: 14px; color: var(--ink);
    white-space: nowrap;
  }
  .intro p + p { margin-top: 11px; }
  .intro .range { margin-top: 14px; }

  .footer {
    position: absolute; left: 0; right: 0; bottom: 0; height: 36px;
    background: var(--brand-blue);
    display: flex; align-items: center; justify-content: center; gap: 11px;
    color: #fff; font-size: 8.4px; white-space: nowrap;
  }
  .footer span { flex: none; }
  .footer span::before {
    content: ""; display: inline-block; width: 4px; height: 4px;
    border-radius: 50%; background: #fff; margin-right: 3px; vertical-align: 1px;
  }
  .footer .footer__name::before { display: none; }

  .tagline {
    position: absolute; right: 27px; top: 30px;
    text-align: right; font-weight: 300; font-size: 14.5px; line-height: 19px;
    color: var(--muted);
  }

  .page--back .ornament { left: 28px; top: 135px; width: 158px; height: 196px; border-radius: 28px; }
  .page--back .frame { left: 52px; top: 163px; width: 109px; height: 140px; border-width: 3px; }
  .page--back .photo {
    left: 13px; top: 12px; width: 77px; height: 110px;
    background: radial-gradient(circle at 50% 55%, #e3a546 0%, #dfe8e6 55%, #b9c4c6 100%);
  }

  .feature { position: absolute; left: 247px; top: 138px; width: 200px; }
  .feature__title {
    font-family: "Great Vibes", cursive; font-weight: 400;
    font-size: 31px; color: var(--brand-blue); line-height: 34px;
  }
  .feature__text { font-size: 9.4px; line-height: 12.6px; color: var(--brand-gold); margin-top: 3px; }
  .feature__text .highlight { color: var(--brand-blue); }

  .story {
    position: absolute; left: 28px; right: 16px; top: 358px;
    font-size: 9.2px; line-height: 12.6px; color: var(--ink);
  }
  .story p + p { margin-top: 12px; }
</style>
</head>
<body>

<section class="page page--front">
  <div class="brand"><span class="brand__dot"></span>Wattle Lantern</div>
  <div class="ornament" role="img" aria-label="Gold ornamental scrollwork surrounding the product frame"></div>
  <div class="frame">
    <div class="photo" role="img" aria-label="Photograph of a hand-painted glass pendant showing a bush landscape with wildflowers, hanging on a silver chain">
      <p class="photo-caption">unique<br>internally hand-painted<br>&amp;<br>beautiful</p>
    </div>
  </div>
  <div class="intro">
    <p>Wattle Lantern Pty Ltd is proud to produce a unique range of HAND-PAINTED glass ornaments.<br>
    The designs are reproduced exclusively for Wattle Lantern Pty Ltd. Our current range includes:</p>
    <p class="range">AUSTRALIAN INDIGENOUS: aboriginal design</p>
    <p>TRADITIONAL AUSTRALIAN: non-Indigenous</p>
    <p>CORPORATE: Company logo or design</p>
  </div>
  <footer class="footer">
    <span class="footer__name">WATTLE LANTERN</span>
    <span>PO BOX 4870. BRISBANE. QLD. 4000</span>
    <span>PH: +61-7-35550142</span>
    <span>FAX: +61-7-35550187</span>
  </footer>
</section>

<section class="page page--back">
  <div class="brand"><span class="brand__dot"></span>Wattle Lantern</div>
  <p class="tagline">unique<br>internally hand-painted<br>&amp;<br>beautiful</p>
  <div class="ornament" role="img" aria-label="Gold ornamental scrollwork surrounding the ornament frame"></div>
  <div class="frame">
    <div class="photo" role="img" aria-label="Photograph of a glass bauble internally painted with a desert spinifex design"></div>
  </div>
  <div class="feature">
    <h2 class="feature__title">Uluru</h2>
    <p class="feature__text">Uluru, also known as <span class="highlight">Ayers Rock</span> stands 348 metres high and changes colour at sunrise and sunset. Uluru is listed as a World Heritage site and is a sacred part of Aboriginal Dreamtime.</p>
  </div>
  <div class="story">
    <p>Our ornaments beautifully represent all things which are uniquely Australian.<br>
    They are an ideal gift for loved ones or just perfect for decorating a favourite place at home, office or family Christmas tree. Similarly, collectors will find the allure of these hand-crafted items irresistible.</p>
    <p>These internal-painted glass ornaments are a keepsake to be treasured from generation to generation. Each ornament is presented in its own padded gift box. This presentation gift box is covered in a beautiful Australian Aboriginal design fabric.</p>
  </div>
  <footer class="footer">
    <span class="footer__name">WATTLE LANTERN</span>
    <span>PO BOX 4870. BRISBANE. QLD. 4000</span>
    <span>PH: +61-7-35550142</span>
    <span>FAX: +61-7-35550187</span>
  </footer>
</section>

</body>
</html>
```